Velmora Consulting Business

** Please add the content information from my old business card
1. I would like to see a two sided business card with both options with the 1st Option--Tallow Spire-new WHITE BACKGROUND LOGO
2 nd Option-Tallow Spire - new BLACK- Background Logo
3rd -Option a business card with my Photo on the card
Please add the new word to the card information:
EXECUTION
AS THE OWNER'S REP
WE AIM TO ACHIEVE YOUR
INFRASTRUCTURE VISION with
OUR SPECIALIZATION & EXECUTION in:

FUNDING Planning
BUSINESS Planning
INFRASTRUCTURE Planning
PROJECT Management
Since 2012
_____________________________________________________________________
I want to get spot uv raised printing. I was liking a a nice rich white linen paper stock with black writing & NOT A COLORED CARD other than a variety of white or black cards concept

```html
<!DOCTYPE html>
<html lang="en">
<head>
<meta charset="utf-8">
<title>Velmora Consulting – Business Card</title>
<link rel="stylesheet" href="https://fonts.googleapis.com/css2?family=Montserrat:wght@400;500;700&family=Tinos&display=swap">
<style>
  :root {
    --stage: #1b1b1b;
    --card-dark: #231f20;
    --card-back: #141414;
    --paper: #ffffff;
    --red: #e31b3b;
    --ink: #1e1e1e;
    --silver: #b9b9b9;
    --faint: #2a2a2a;
  }
  * { box-sizing: border-box; margin: 0; padding: 0; }
  html, body { width: 1200px; height: 1059px; overflow: hidden; }
  body { background: var(--stage); position: relative; font-family: "Montserrat", sans-serif; }

  .card { position: absolute; border-radius: 18px; overflow: hidden; }

  /* Front */
  .card-front { left: 257px; top: 91px; width: 688px; height: 389px; background: var(--card-dark); }
  .card-front .edge { position: absolute; inset: 0; }
  .card-front .face { position: absolute; left: 14px; right: 16px; top: 7px; bottom: 0; background: var(--paper); }

  .brand { position: absolute; display: flex; align-items: center; gap: 10px; }
  .brand-mark { width: 14px; height: 14px; background: var(--red); flex: none; }
  .brand-name { font-weight: 700; line-height: 1.1; }
  .card-front .brand { left: 70px; top: 150px; }
  .card-front .brand-name { font-size: 25px; color: var(--ink); }

  .divider { position: absolute; width: 2px; background: var(--red); }
  .card-front .divider { left: 309px; top: 130px; height: 151px; }

  .person-name { position: absolute; left: 322px; top: 130px; font-size: 21px; font-weight: 700; color: var(--red); white-space: nowrap; }
  .person-role { position: absolute; left: 322px; top: 159px; font-size: 12px; font-weight: 500; color: var(--ink); letter-spacing: .2px; }
  .locations { position: absolute; left: 328px; top: 193px; font-size: 14px; font-weight: 500; color: var(--ink); }
  .contact-list { position: absolute; left: 326px; top: 220px; list-style: none; }
  .contact-list li { display: flex; align-items: center; gap: 12px; height: 20.5px; font-size: 14px; font-weight: 500; color: var(--ink); }
  .contact-list svg { width: 15px; height: 13px; flex: none; fill: var(--red); }

  /* Back */
  .card-back { left: 252px; top: 546px; width: 710px; height: 394px; background: var(--card-back); }
  .card-back .brand { left: 100px; top: 160px; }
  .card-back .brand-name { font-size: 34px; color: var(--silver); }
  .card-back .divider { left: 376px; top: 82px; height: 243px; }

  .mission { position: absolute; left: 390px; top: 86px; font-family: "Tinos", serif; font-size: 15.5px; line-height: 20.5px; color: var(--red); text-transform: uppercase; white-space: nowrap; }
  .mission .lower { text-transform: none; }
  .mission strong { font-family: "Montserrat", sans-serif; font-weight: 700; font-size: 15px; }

  .services { position: absolute; left: 390px; top: 202px; list-style: none; }
  .services li { display: flex; align-items: center; gap: 16px; height: 32px; font-size: 15.5px; font-weight: 500; color: #f2f2f2; letter-spacing: .3px; }
  .services li::before { content: ""; width: 9px; height: 9px; background: var(--red); transform: rotate(45deg); margin-left: 4px; }

  .since { position: absolute; left: 577px; top: 363px; font-size: 14px; color: var(--faint); }
</style>
</head>
<body>

<section class="card card-front" aria-label="Business card front">
  <svg class="edge" viewBox="0 0 688 389" preserveAspectRatio="none" aria-hidden="true">
    <polygon points="0,0 14,0 14,208 0,190" fill="var(--red)"/>
    <polygon points="672,0 688,0 688,186 672,168" fill="var(--red)"/>
    <polygon points="0,192 14,210 14,216 0,198" fill="#ffffff"/>
    <polygon points="672,170 688,188 688,194 672,176" fill="#ffffff"/>
  </svg>
  <div class="face"></div>

  <div class="brand">
    <span class="brand-mark"></span>
    <span class="brand-name">Velmora<br>Consulting</span>
  </div>

  <div class="divider"></div>
  <h1 class="person-name">Marlene Ostrowski-Vance</h1>
  <p class="person-role">CEO / LEAD PROJECT MANAGER</p>
  <p class="locations">Northbay NT • Eastmere NB</p>
  <ul class="contact-list">
    <li><svg viewBox="0 0 16 14"><path d="M1 5c0-3 14-3 14 0v1.5h-3.5V5c-2-1-5-1-7 0v1.5H1z"/><path d="M4 7h8l2 6H2z"/></svg>867.555.0148</li>
    <li><svg viewBox="0 0 16 14"><path d="M1 2h14v1.5L8 8 1 3.5z"/><path d="M1 5l7 4.5L15 5v7H1z"/></svg>marlene@velmora.ca</li>
    <li><svg viewBox="0 0 16 16"><circle cx="8" cy="8" r="7.5"/><path d="M4 5c2 0 3 1 2.5 3S8 10 7 13M10 2.5c0 2 2 2 3.5 3" stroke="#fff" stroke-width="1.3" fill="none"/></svg>www.velmora.ca</li>
  </ul>
</section>

<section class="card card-back" aria-label="Business card back">
  <div class="brand">
    <span class="brand-mark"></span>
    <span class="brand-name">Velmora<br>Consulting</span>
  </div>

  <div class="divider"></div>
  <p class="mission">
    As the <strong>OWNER'S REP</strong><br>
    We aim to achieve your<br>
    Infrastructure vision <span class="lower">with</span><br>
    Our specialization <span class="lower">in:</span>
  </p>
  <ul class="services">
    <li>FUNDING Planning</li>
    <li>BUSINESS Planning</li>
    <li>INFRASTRUCTURE Planning</li>
    <li>PROJECT Management</li>
  </ul>
  <p class="since">Since 2012</p>
</section>

</body>
</html>
```